I have a business that exists already (Linden Conservatory of Music) that we offer music lessons to all instruments. I recently opened a smaller version called CHORDS by Linden that will only teach piano lessons. What I'm looking for now is a 3 page Website on word press. After I choose the design I like I want to be able to take over the website and bring it to our hosting company. We want full control of it and our team will take over. The reason I'm doing this is to have other visions and ideas from others. The first page will be about the company and our message/vision. Second page about the piano lessons. The third will be about franchising this concept "Chords by Linden" Attached are 3 Logos . Please refer to our existing website www.lindenmusicconservatory.example to look at our piano page and franchising page. Please feel free to message me if you need more info. Thanks
Please note I do not want the new website (Chords by Linden) To look like the other Website (Linden Conservatory of Music) Fresh new look. I do not want the colours red or using the Red logo. I only provided it so that you have an Idea of What the other business looks like and that you can take the piano content and franchise content off of it. Chords by Linden is smaller concept and only piano lessons.
Thanks
Only Piano lessons for all students
3 page

```html
<!DOCTYPE html>
<html lang="en">
<head>
<meta charset="utf-8">
<title>Chords by Linden — Piano Lessons</title>
<link rel="stylesheet" href="https://fonts.googleapis.com/css2?family=Cinzel:wght@400;500&family=Great+Vibes&family=Montserrat:wght@400;500&display=swap">
<style>
  :root {
    --gold: #e6c463;
    --gold-deep: #d9b24a;
    --ink: #111111;
    --night: #141414;
    --mist: #ececec;
    --white: #ffffff;
    --text: #2b2b2b;
    --muted: #555555;
    --heading: "Cinzel", serif;
    --body: "Montserrat", sans-serif;
    --script: "Great Vibes", cursive;
  }
  * { box-sizing: border-box; margin: 0; padding: 0; }
  html, body { width: 1200px; height: 2893px; overflow: hidden; }
  body { position: relative; font-family: var(--body); color: var(--text); background: var(--white); }
  .abs { position: absolute; }

  .btn {
    position: absolute; display: flex; align-items: center; justify-content: center;
    font-family: var(--heading); font-size: 14px; font-weight: 500; letter-spacing: .3px;
    width: 115px; height: 36px; border-radius: 2px; text-decoration: none;
  }
  .btn--gold { background: var(--gold); color: var(--ink); }
  .btn--dark { background: var(--ink); color: var(--white); }

  .section-title { font-family: var(--heading); font-weight: 400; color: var(--ink); text-transform: uppercase; }
  .rule { position: absolute; height: 3px; width: 35px; background: var(--gold); }

  /* Navigation */
  .site-nav { left: 0; top: 0; width: 1200px; height: 78px; background: rgba(10,10,10,.88); z-index: 3; }
  .brand { left: 148px; top: 18px; display: flex; align-items: center; gap: 8px; font-family: var(--heading); color: var(--white); font-size: 26px; }
  .brand__dot { width: 10px; height: 10px; background: var(--white); border-radius: 50%; }
  .brand small { font-size: 13px; }
  .nav-links { left: 460px; top: 32px; display: flex; gap: 48px; list-style: none; font-family: var(--heading); font-size: 13px; color: var(--white); }
  .nav-links .is-active { color: var(--gold); }
  .nav-divider { left: 922px; top: 24px; width: 1px; height: 30px; background: #555; }
  .nav-social { left: 950px; top: 34px; display: flex; gap: 22px; }
  .nav-social span { width: 10px; height: 10px; border-radius: 50%; background: var(--gold); }

  /* Hero */
  .hero { left: 0; top: 0; width: 1200px; height: 600px;
    background: linear-gradient(100deg, #3a3a2c 0%, #2a2622 35%, #6b6560 55%, #1d1b1a 75%, #0e0e0e 100%); }
  .hero__script { left: 141px; top: 212px; font-family: var(--script); font-size: 72px; color: var(--gold); }
  .hero__title { left: 141px; top: 300px; font-family: var(--heading); font-size: 54px; font-weight: 400; color: var(--white); letter-spacing: 1px; }

  /* About */
  .about { left: 0; top: 600px; width: 1200px; height: 439px; }
  .about__band { left: 0; top: 0; }
  .about__photo { left: 141px; top: 69px; width: 415px; height: 300px; border-radius: 10px;
    background: linear-gradient(120deg, #d9d2c6 0%, #8b8f93 45%, #3d4d63 70%, #2b2b2d 100%); }
  .about__text { left: 601px; top: 64px; width: 456px; }
  .about__text h2 { font-size: 26px; }
  .about__text .rule { position: static; display: block; margin: 12px 0 16px; }
  .about__text h3 { font-family: var(--body); font-size: 16px; font-weight: 500; color: #333; margin-bottom: 6px; }
  .about__text p { font-size: 13px; line-height: 19px; text-align: justify; color: #333; }

  /* Vision */
  .vision { left: 0; top: 1039px; width: 1200px; height: 376px;
    background: linear-gradient(180deg, #efefef 0%, #e8e8e8 60%, #f2f2f2 100%); }
  .vision h2 { left: 0; width: 1200px; top: 62px; text-align: center; font-size: 26px; }
  .vision .rule { left: 583px; top: 106px; }
  .vision p { left: 141px; width: 918px; text-align: center; font-size: 13.5px; line-height: 22px; color: var(--ink); }

  /* Programs */
  .programs { left: 0; top: 1415px; width: 1200px; height: 469px; }
  .programs h2 { left: 141px; top: 64px; font-size: 25px; line-height: 34px; width: 480px; }
  .programs .rule { left: 141px; top: 141px; }
  .program-list { left: 141px; top: 160px; width: 445px; list-style: none; }
  .program-list li { position: relative; padding-left: 26px; font-size: 13px; line-height: 19px; color: #333; margin-bottom: 9px; }
  .program-list svg { position: absolute; left: 0; top: 3px; }
  .programs__photo { left: 644px; top: 67px; width: 414px; height: 327px; border-radius: 10px;
    background: linear-gradient(110deg, #1a1a1a 0%, #3b3b3b 30%, #f2eee8 45%, #e9e2d8 75%, #c9b48f 100%); }

  /* Franchise */
  .franchise { left: 0; top: 1884px; width: 1200px; height: 269px;
    background: linear-gradient(180deg, #e9e9e9 0%, #efefef 50%, #e4e4e4 100%); }
  .franchise h2 { left: 0; width: 1200px; top: 60px; text-align: center; font-size: 34px; }
  .franchise p { left: 0; width: 1200px; top: 132px; text-align: center; font-size: 16px; color: #444; letter-spacing: .3px; }

  /* Booking */
  .booking { left: 0; top: 2153px; width: 1200px; height: 476px; background: #474747; }
  .booking__photo { left: 0; top: 0; width: 1200px; height: 180px;
    background: linear-gradient(180deg, #1b1b1b 0%, #2c2c2c 60%, #3a3a3a 100%); }
  .booking h2 { left: 0; width: 1200px; top: 75px; text-align: center; font-size: 25px; color: var(--white); }
  .booking .rule { left: 583px; top: 117px; }
  .booking__card { left: 141px; top: 137px; width: 917px; height: 271px; background: var(--white); }
  .field { position: absolute; background: var(--white); box-shadow: 0 1px 5px rgba(0,0,0,.14); border-radius: 2px;
    font-size: 11px; color: #666; padding: 16px 13px; }
  .booking .btn { left: 401px; top: 200px; }

  /* Contact */
  .contact { left: 0; top: 2629px; width: 1200px; height: 264px; background: var(--gold); }
  .contact-item { width: 300px; text-align: center; }
  .contact-item h4 { font-family: var(--heading); font-weight: 400; font-size: 15px; color: var(--ink); margin-top: 10px; }
  .contact-item p { font-size: 12.5px; line-height: 20px; color: var(--ink); margin-top: 2px; }
  .contact .divider { left: 141px; top: 211px; width: 917px; height: 1px; background: rgba(0,0,0,.2); }
  .copyright { left: 141px; top: 232px; font-size: 12.5px; color: var(--ink); }
  .footer-social { left: 949px; top: 224px; display: flex; gap: 8px; }
  .footer-social span { width: 32px; height: 32px; border-radius: 50%; background: var(--ink); }
</style>
</head>
<body>

  <section class="hero abs" role="img" aria-label="Photo of hands playing a grand piano keyboard"></section>

  <header class="site-nav abs">
    <div class="brand abs"><span class="brand__dot"></span>CHORDS <small>by Linden</small></div>
    <ul class="nav-links abs">
      <li class="is-active">HOME</li>
      <li>PIANO LESSONS</li>
      <li>FRANCHISING</li>
      <li>CONTACT US</li>
    </ul>
    <div class="nav-divider abs"></div>
    <div class="nav-social abs" aria-label="Social links"><span></span><span></span><span></span><span></span></div>
  </header>

  <div class="hero__script abs">Welcome to</div>
  <h1 class="hero__title abs">CHORDS BY LINDEN</h1>
  <a class="btn btn--gold" style="left:141px;top:389px;">READ MORE</a>

  <section class="about abs">
    <svg class="about__band abs" width="1200" height="439" viewBox="0 0 1200 439">
      <polygon points="562,0 1200,0 1200,439 452,439" fill="var(--gold)"/>
    </svg>
    <div class="about__photo abs" role="img" aria-label="Photo of a young man in headphones playing a keyboard in a home studio"></div>
    <div class="about__text abs">
      <h2 class="section-title">About Us</h2>
      <span class="rule" style="background:var(--ink)"></span>
      <h3>Playing The Piano</h3>
      <p>When you think of a piano, you probably envision black and white keys but the piano is more than those harmonious sounds created by the player. The versatility and the musicianship instilled into the player from those keys is the true magic that comes from playing piano! Starting from the grassroots, experience different methods and styles of playing piano. To mark the milestones of progression, engage in one of Linden's many unique performance opportunities like annual festival competitions, recitals or our examinations (Linden &amp; NCM). Penultimately,</p>
    </div>
    <a class="btn btn--dark" style="left:600px;top:333px;">READ MORE</a>
  </section>

  <section class="vision abs" role="img" aria-label="Soft faded photo of piano keys">
    <h2 class="section-title abs">Our Vision</h2>
    <span class="rule"></span>
    <p class="abs" style="top:120px;">Our Mission Lorem ipsum dolor sit amet, consectetur adipiscing elit, sed do eiusmod tempor incididunt ut labore et dolore magna aliqua. Ut enim ad minim veniam, quis nostrud exercitation ullamco laboris nisi ut aliquip ex ea commodo consequat. Duis aute irure dolor in reprehenderit in voluptate velit esse cillum dolore eu fugiat nulla pariatur. Excepteur sint occaecat cupidatat non proident, sunt in culpa qui officia deserunt mollit anim id est laborum.</p>
    <p class="abs" style="top:212px;">Ut enim ad minim veniam, quis nostrud exercitation ullamco laboris nisi ut aliquip ex ea commodo consequat. Duis aute irure dolor in reprehenderit in voluptate velit esse cillum dolore eu fugiat nulla pariatur.</p>
    <a class="btn btn--gold" style="left:543px;top:269px;">READ MORE</a>
  </section>

  <section class="programs abs">
    <svg class="abs" style="left:0;top:0" width="1200" height="469" viewBox="0 0 1200 469">
      <polygon points="0,0 719,0 826,469 0,469" fill="var(--gold)"/>
    </svg>
    <h2 class="section-title abs">Our programs also provide students the opportunity to:</h2>
    <span class="rule" style="background:var(--ink)"></span>
    <ul class="program-list abs">
      <li><svg width="14" height="12" viewBox="0 0 14 12"><path d="M1 6h11M8 2l4 4-4 4" fill="none" stroke="#222" stroke-width="1.5"/></svg>Participate in large-scale performances.</li>
      <li><svg width="14" height="12" viewBox="0 0 14 12"><path d="M1 6h11M8 2l4 4-4 4" fill="none" stroke="#222" stroke-width="1.5"/></svg>Perform at Linden's many community events on a regular basis.</li>
      <li><svg width="14" height="12" viewBox="0 0 14 12"><path d="M1 6h11M8 2l4 4-4 4" fill="none" stroke="#222" stroke-width="1.5"/></svg>Access the GTA's coolest Broadcast stage</li>
      <li><svg width="14" height="12" viewBox="0 0 14 12"><path d="M1 6h11M8 2l4 4-4 4" fill="none" stroke="#222" stroke-width="1.5"/></svg>Attend Clinics, Masterclasses, and Jam Nights</li>
      <li><svg width="14" height="12" viewBox="0 0 14 12"><path d="M1 6h11M8 2l4 4-4 4" fill="none" stroke="#222" stroke-width="1.5"/></svg>Access the Linden Rocks band program. Linden's Band Program empowers and electrifies students to come together, create music and confidently hit the stage with their own band identity while having fun and honing their instrument.</li>
    </ul>
    <a class="btn btn--dark" style="left:141px;top:360px;">READ MORE</a>
    <div class="programs__photo abs" role="img" aria-label="Photo of hands in a cream sweater playing piano keys"></div>
  </section>

  <section class="franchise abs" role="img" aria-label="Soft faded photo of hands on a piano">
    <h2 class="section-title abs">Franchise Opportunities</h2>
    <p class="abs">Be Part Of The Linden Conservatory Family</p>
    <a class="btn btn--gold" style="left:543px;top:164px;">READ MORE</a>
  </section>

  <section class="booking abs">
    <div class="booking__photo abs" role="img" aria-label="Dark photo of piano keys"></div>
    <h2 class="section-title abs">Book a meeting with us</h2>
    <span class="rule"></span>
    <form class="booking__card abs">
      <div class="field" style="left:48px;top:33px;width:267px;height:36px;padding-top:12px;">Your Name*</div>
      <div class="field" style="left:325px;top:33px;width:267px;height:36px;padding-top:12px;">Your Phone*</div>
      <div class="field" style="left:605px;top:33px;width:267px;height:36px;padding-top:12px;">Your Email*</div>
      <div class="field" style="left:48px;top:83px;width:824px;height:90px;padding-top:14px;">Your Message*</div>
      <a class="btn btn--gold">SUBMIT</a>
    </form>
  </section>

  <footer class="contact abs">
    <div class="contact-item abs" style="left:106px;top:50px;">
      <svg width="44" height="44" viewBox="0 0 24 24"><path d="M6.6 10.8c1.4 2.8 3.8 5.1 6.6 6.6l2.2-2.2c.3-.3.7-.4 1-.2 1.1.4 2.3.6 3.6.6.6 0 1 .4 1 1V20c0 .6-.4 1-1 1C10.6 21 3 13.4 3 4c0-.6.4-1 1-1h3.5c.6 0 1 .4 1 1 0 1.3.2 2.5.6 3.6.1.3 0 .7-.2 1L6.6 10.8z" fill="var(--ink)"/></svg>
      <h4>CALL US</h4>
      <p>1-800-555-0142</p>
    </div>
    <div class="contact-item abs" style="left:450px;top:42px;">
      <svg width="40" height="52" viewBox="0 0 24 32"><path d="M12 0C5.4 0 0 5.3 0 11.9 0 20.6 12 32 12 32s12-11.4 12-20.1C24 5.3 18.6 0 12 0zm0 17a5 5 0 110-10 5 5 0 010 10z" fill="var(--ink)"/></svg>
      <h4>POSTAL ADDRESS</h4>
      <p>123, Lorem ipsum dolor sit 123456<br>#123456 Lorem ipsum</p>
    </div>
    <div class="contact-item abs" style="left:761px;top:56px;">
      <svg width="46" height="36" viewBox="0 0 46 36"><rect x="0" y="0" width="46" height="36" rx="2" fill="var(--ink)"/><path d="M2 3l21 16L44 3" fill="none" stroke="var(--gold)" stroke-width="3"/></svg>
      <h4>E-MAIL</h4>
      <p>info@chordslindenmusic.example</p>
    </div>
    <div class="divider abs"></div>
    <p class="copyright abs">Copyright 2019. Chordslinden Music Training. All rights reserved.</p>
    <div class="footer-social abs" aria-label="Social links"><span></span><span></span><span></span></div>
  </footer>

</body>
</html>
```